Wholesale in Gold Jewellery & Gold Bullion

We are an established gold jewellery and gold bullion wholesaler selling these products to international clients. We already have a name and logo of our company, hence please view attached current card design. We need a completely new design to compliment our business and industry and the final design should be new and elegant.

Contact Information for Business Card

New card details must be same as per current card. Like logo, name, tel no. & etc.

Colors

Designer to choose colors to be used in the design.

```html
<!DOCTYPE html>
<html lang="en">
<head>
<meta charset="utf-8">
<title>Orvane &amp; Co – Business Card</title>
<link rel="stylesheet" href="https://fonts.googleapis.com/css2?family=Lato:wght@400;700&family=Tinos:wght@700&display=swap">
<style>
  :root {
    --backdrop: #e4e2dd;
    --card: #ffffff;
    --gold: #c4922f;
    --ink: #111111;
    --text: #1e1e1e;
  }
  * { margin: 0; padding: 0; box-sizing: border-box; }
  html, body { width: 1200px; height: 843px; overflow: hidden; }
  body {
    background: var(--backdrop);
    display: flex;
    align-items: center;
    justify-content: center;
    font-family: "Lato", Arial, sans-serif;
  }
  .card {
    position: relative;
    width: 1000px;
    height: 572px;
    background: var(--card);
    box-shadow: 0 6px 24px rgba(0,0,0,0.12);
    overflow: hidden;
  }
  .company-name {
    position: absolute;
    left: 52px;
    top: 52px;
    font-family: "Tinos", "Times New Roman", serif;
    font-weight: 700;
    font-size: 54px;
    letter-spacing: 1px;
    color: var(--ink);
    white-space: nowrap;
  }
  .accent-bar {
    position: absolute;
    left: 0;
    top: 196px;
    width: 12px;
    height: 84px;
    background: var(--gold);
  }
  .person { position: absolute; left: 76px; top: 178px; color: var(--text); }
  .person-name { font-size: 44px; font-weight: 400; line-height: 1.1; }
  .person-title { font-size: 34px; font-weight: 400; line-height: 1.2; margin-left: 14px; }
  .rules { position: absolute; left: 0; top: 0; width: 1000px; height: 572px; }
  .brand-mark {
    position: absolute;
    left: 640px;
    top: 210px;
    display: flex;
    align-items: center;
    gap: 14px;
  }
  .brand-dot { width: 34px; height: 34px; border-radius: 50%; background: var(--gold); }
  .brand-word {
    font-family: "Lato", Arial, sans-serif;
    font-weight: 700;
    font-size: 40px;
    letter-spacing: 3px;
    color: var(--gold);
  }
  .contacts {
    position: absolute;
    left: 104px;
    top: 400px;
    list-style: none;
    font-size: 29px;
    color: var(--text);
    line-height: 40px;
  }
  .contacts li { display: flex; align-items: center; gap: 14px; }
  .contacts svg { width: 26px; height: 26px; fill: var(--gold); flex: none; }
  .address {
    position: absolute;
    right: 44px;
    top: 410px;
    font-size: 29px;
    line-height: 40px;
    color: var(--text);
    text-align: right;
  }
</style>
</head>
<body>
  <section class="card">
    <h1 class="company-name">ORVANE &amp; CO PTE LTD</h1>
    <div class="accent-bar"></div>
    <div class="person">
      <p class="person-name">Arjun Kalvani</p>
      <p class="person-title">Director</p>
    </div>

    <svg class="rules" viewBox="0 0 1000 572" aria-hidden="true">
      <g stroke="var(--gold)" stroke-width="4">
        <line x1="120" y1="332" x2="620" y2="250"/>
        <line x1="128" y1="356" x2="628" y2="274"/>
        <line x1="880" y1="214" x2="985" y2="196"/>
        <line x1="884" y1="236" x2="989" y2="218"/>
      </g>
    </svg>

    <div class="brand-mark">
      <span class="brand-dot"></span>
      <span class="brand-word">ORVANE</span>
    </div>

    <ul class="contacts">
      <li>
        <svg viewBox="0 0 24 24"><path d="M6.6 10.8a15.1 15.1 0 0 0 6.6 6.6l2.2-2.2c.3-.3.7-.4 1-.2 1.1.4 2.3.6 3.6.6.6 0 1 .4 1 1V20c0 .6-.4 1-1 1A17 17 0 0 1 3 4c0-.6.4-1 1-1h3.5c.6 0 1 .4 1 1 0 1.3.2 2.5.6 3.6.1.3 0 .7-.2 1z"/></svg>
        <span>+65 6100 2400</span>
      </li>
      <li>
        <svg viewBox="0 0 24 24"><path d="M7 1h10a2 2 0 0 1 2 2v18a2 2 0 0 1-2 2H7a2 2 0 0 1-2-2V3a2 2 0 0 1 2-2zm0 3v14h10V4zm5 15.5a1.2 1.2 0 1 0 0 2.4 1.2 1.2 0 0 0 0-2.4z"/></svg>
        <span>+65 9100 3521</span>
      </li>
      <li>
        <svg viewBox="0 0 24 24"><path d="M6 2h12v6H6zM4 9h16a2 2 0 0 1 2 2v7h-4v4H6v-4H2v-7a2 2 0 0 1 2-2zm4 7v4h8v-4z"/></svg>
        <span>+65 6100 2418</span>
      </li>
      <li>
        <svg viewBox="0 0 24 24"><path d="M2 5h20v14H2zm2 2v.5l8 5.5 8-5.5V7z"/></svg>
        <span>arjun@orvaneco.com</span>
      </li>
    </ul>

    <address class="address" style="font-style:normal">
      18 Marlow Lane,<br>Singapore 208115
    </address>
  </section>
</body>
</html>
```